Brightline Energy Product Distribution Brochure

We are looking to have our current brochure for our customers completely redesigned...the idea is to present the relevant information in an attractive way . Our website is brightlineenergyco.example where you can find more information about us. We have included a file with a rough idea of the page order and what each should include but feel free to adapt based on design. The example provided is only for context and doesnt have to be maintained. We will be using the brochure both digitally and in print form. As long as it reads easily and is eye catching, the design can be horizontal or vertical.Final deliverable should be indesign file.

"Our Brands" page: should be limited to one page (space being enough) where it has the header for each one (for example diesel generators) space for one or two lines of text and then the corresponding logos for each of the five categories
Updates

For those asking: the "our brands" page should be a single page layout where there is a header with the corresponding section and space for maybe one line of text followed by the two logos for that category. Each of the product pages should be similar in fashion to the one in the document attached: a photo of the product with some white space and space for the text to be included. We will be posting additional examples today

Target Market(s)

We want to present it to customers both digitally and in print so they can see our products

Industry/Entity Type

Power Generation

Font styles to use
Serif

Requirements
Must have
• Eye catching and able to present the information in a presentable fashion. Rest is up to you.
Nice to have
• Should incorporate the colors of our logo but can also add other depending on design

```html
<!DOCTYPE html>
<html lang="en">
<head>
<meta charset="utf-8">
<title>Distributor Program Guide – Brightline Energy</title>
<link href="https://fonts.googleapis.com/css2?family=Barlow:ital,wght@0,400;0,600;0,800;1,600;1,800&display=swap" rel="stylesheet">
<style>
  :root {
    --brand-yellow: #fcc30b;
    --ink: #3a3a3c;
    --ink-soft: #58595b;
    --paper: #ffffff;
    --backdrop: #c9c9c9;
    --photo-dusk: #5a6a86;
    --photo-glow: #e39a2a;
    --photo-shadow: #2a2a36;
  }
  html, body {
    margin: 0;
    width: 1200px;
    height: 857px;
    overflow: hidden;
    background: var(--backdrop);
    font-family: "Barlow", Arial, sans-serif;
  }
  .cover {
    position: absolute;
    left: 317px;
    top: 28px;
    width: 566px;
    height: 800px;
    background: var(--paper);
    overflow: hidden;
    box-shadow: 0 6px 18px rgba(0,0,0,0.18);
  }
  .cover-shapes {
    position: absolute;
    inset: 0;
  }
  .cover-photo {
    position: absolute;
    left: 0;
    top: 195px;
    width: 566px;
    height: 380px;
    background:
      radial-gradient(ellipse at 70% 75%, rgba(255,200,90,0.85), transparent 45%),
      radial-gradient(ellipse at 35% 65%, rgba(227,154,42,0.7), transparent 50%),
      linear-gradient(180deg, var(--photo-dusk) 0%, #6d6f7f 30%, var(--photo-glow) 70%, var(--photo-shadow) 100%);
  }
  .title-block {
    position: absolute;
    left: 38px;
    top: 30px;
    color: var(--ink);
  }
  .guide-title {
    margin: 0;
    font-weight: 800;
    font-style: italic;
    font-size: 31px;
    line-height: 1.02;
    letter-spacing: 0.2px;
    text-transform: uppercase;
  }
  .title-rule {
    width: 64px;
    height: 3px;
    background: var(--brand-yellow);
    margin: 12px 0 14px;
  }
  .guide-subtitle {
    margin: 0;
    font-weight: 600;
    font-style: italic;
    font-size: 19px;
    line-height: 1.15;
    text-transform: uppercase;
  }
  .contact {
    position: absolute;
    left: 34px;
    top: 630px;
    font-size: 11px;
    line-height: 1.35;
    color: var(--ink);
  }
  .contact .phone {
    margin-top: 6px;
    font-weight: 800;
    font-size: 11.5px;
  }
  .brand-lockup {
    position: absolute;
    left: 268px;
    top: 690px;
    display: flex;
    align-items: center;
    gap: 10px;
  }
  .brand-mark {
    width: 26px;
    height: 26px;
    background: var(--brand-yellow);
  }
  .brand-name {
    font-weight: 600;
    font-size: 25px;
    color: var(--ink);
    letter-spacing: 0.5px;
    text-transform: uppercase;
  }
</style>
</head>
<body>
  <article class="cover">
    <svg class="cover-shapes" width="566" height="800" viewBox="0 0 566 800" aria-hidden="true">
      <polygon points="410,0 566,0 566,195 310,195" fill="var(--brand-yellow)"/>
      <polygon points="0,575 225,575 128,786 0,786" fill="var(--brand-yellow)"/>
      <rect x="0" y="786" width="566" height="14" fill="var(--ink-soft)"/>
    </svg>

    <div class="cover-photo" role="img" aria-label="Photo of an industrial power plant lit up at dusk"></div>

    <header class="title-block">
      <h1 class="guide-title">Distributor<br>Program Guide</h1>
      <div class="title-rule"></div>
      <p class="guide-subtitle">Diesel Generators<br>Alternators &amp; Parts</p>
    </header>

    <address class="contact" style="font-style: normal;">
      Brightline Energy Limited, Inc.<br>
      4420 Harbor Works Avenue<br>
      Portside, FL 30000, USA
      <div class="phone">1-800-555-0147</div>
    </address>

    <div class="brand-lockup">
      <span class="brand-mark"></span>
      <span class="brand-name">Brightline Energy</span>
    </div>
  </article>
</body>
</html>
```